Mobile App Flyer for Takeaway Tappora

We need a single A4 page flyer to promote our mobile apps for takeaway food solution.

Please visit our web site www.tappora-demo.com and review the retail page for further details but here are a number of the benefits that I'd like to try to include in the flyer.

I do need a catchy title too...

TAKEAWAYS & RESTAURANTS
Tap into the growth market of mobile and online food ordering. With over 51% of UK online ecommerce sales now being conducted on mobiles devices* it’s crucial takeaways and restaurants adopt a suitable mobile strategy.
* Source: QVLD / Brelwick 2016
Stay independent. Go mobile with an online food ordering app that is dedicated and designed specifically for your business. Unlike other solutions, we don’t encourage your customer to use a shared app that then promotes your competitors’ businesses to your customers!
We don’t charge order commission, just a small fixed monthly fee, (pricing published on our web site). As you grow your mobile business you keep all the profits!
Benefit from better Zintaro search results. Did you know Zintaro now favours and ranks businesses with mobile apps higher than those without?
Differentiate your business against other local businesses, create a buzz around your business going “Mobile”!
Free-up your business phone line at peak periods, never miss another order.
Save staff time by accepting unlimited mobile and on-line orders simultaneously, no need to take a call and write the orders down, it also minimises mistakes.
If you buy our Business or Business Plus package we will also provide you an online shop that can be added to your website!
If you’re thinking this isn’t going to be cheap, check our pricing on our web site, you’re going to be very pleasantly surprised.
Attractive interactive menus, show-off your business and food to its best.
Convenience for your customers:
No more holding or busy signal when trying to place an order.
Customer’s order history is saved in the app making re-ordering fast and convenient.
Customers can use convenient online payment providers such as KOINRA, as well as traditional credit cards or of course, cash-on-collection.
Easily and quickly update your menu with seasonal changes, menu items, pricing and even delivery options.
Send promotions to your customers and advise them of seasonal opening times, even message them each time they are close to your business!
Launch an in-app loyalty programme, which rewards your loyal customers and generates repeat business.
There are many reason you should be considering going mobile if. Please call us on 01632 960417 or email us at Info@Tappora-demo.com to discuss your requirements with us.

Target Market(s)

Owners of takeaways and restaurants

Font styles to use
Sans Serif

Colors
33b8a4
3176b5
faa54b

Requirements
Must have
• Tap Pora white and blue logo from website
• Features doc has some screen shots that could be used.
• The format must be reusable for other products so if I develop an app for a golf course, for example, I could use the same layout but change the primary colour of the flyer.
• Doesn't have to be identical to web site but shouldn't be poles apart so that it looks odd!
Nice to have
• At least one picture of a smart phone.

```html
<!DOCTYPE html>
<html lang="en">
<head>
<meta charset="utf-8">
<title>Takeaway – Food Retail Solution | Tappora</title>
<link href="https://fonts.googleapis.com/css2?family=Open+Sans:wght@400;600;700;800&display=swap" rel="stylesheet">
<style>
  :root {
    --primary: #33b8a4;
    --primary-dark: #2a9d8c;
    --blue: #3176b5;
    --accent: #faa54b;
    --charcoal: #333638;
    --text: #55595c;
    --icon: #6b7074;
    --white: #ffffff;
  }
  * { margin: 0; padding: 0; box-sizing: border-box; }
  html, body { width: 849px; height: 1200px; overflow: hidden; background: var(--white); }
  body { font-family: "Open Sans", Arial, sans-serif; color: var(--text); }

  .flyer { position: relative; width: 849px; height: 1200px; overflow: hidden; background: var(--white); }

  .hero-photo {
    position: absolute; left: 0; top: 0; width: 849px; height: 540px;
    background:
      radial-gradient(ellipse 320px 240px at 560px 260px, #b5622c 0%, #7a3a1c 45%, transparent 75%),
      radial-gradient(ellipse 200px 150px at 150px 90px, #d9a25a 0%, #9b4a26 55%, transparent 80%),
      radial-gradient(ellipse 140px 260px at 760px 400px, #2c2f33 0%, #3e4246 60%, transparent 85%),
      linear-gradient(160deg, #5a3a28 0%, #3f2a1f 45%, #7b6650 100%);
  }

  .title-block { position: absolute; left: 0; top: 398px; }
  .title-main {
    display: block; width: 310px; height: 54px; padding-left: 30px;
    background: var(--charcoal); color: var(--white);
    font-weight: 800; font-size: 34px; line-height: 54px; letter-spacing: 1px;
  }
  .title-sub {
    display: block; width: 420px; height: 48px; margin-top: 6px; padding-left: 30px;
    background: var(--primary); color: var(--white);
    font-weight: 400; font-size: 25px; line-height: 48px; letter-spacing: 0.5px;
  }

  .benefit-group { position: absolute; display: flex; gap: 14px; }
  .benefit-icon { flex: 0 0 38px; width: 38px; height: 38px; margin-top: 2px; }
  .benefit-list { list-style: none; font-size: 11.6px; line-height: 1.38; }
  .benefit-list li { position: relative; padding-left: 13px; margin-bottom: 2px; }
  .benefit-list li::before {
    content: ""; position: absolute; left: 0; top: 6px;
    width: 5px; height: 5px; border-radius: 50%; background: var(--primary);
  }

  .group-app { left: 26px; top: 572px; width: 380px; }
  .group-customer { left: 432px; top: 608px; width: 395px; }
  .group-business { left: 26px; top: 838px; width: 380px; }
  .group-pricing { left: 432px; top: 870px; width: 395px; }

  .footer {
    position: absolute; left: 0; top: 1092px; width: 849px; height: 108px;
    background: var(--primary); color: var(--white);
    display: flex; align-items: center; justify-content: space-between;
    padding: 0 42px 0 40px;
  }
  .footer-text { font-size: 15.5px; line-height: 1.5; }
  .brand {
    display: flex; align-items: center; gap: 8px;
    background: var(--white); padding: 12px 20px; border-radius: 4px;
  }
  .brand-mark { width: 16px; height: 16px; border-radius: 50%; background: var(--blue); }
  .brand-name { font-weight: 700; font-size: 30px; color: var(--blue); letter-spacing: -0.5px; }
</style>
</head>
<body>
<main class="flyer">
  <div class="hero-photo" role="img" aria-label="Photo of a pizza and a burger on a table with a smartphone showing a food ordering app"></div>

  <header class="title-block">
    <h1 class="title-main">TAKEAWAY</h1>
    <h2 class="title-sub">FOOD RETAIL SOLUTION</h2>
  </header>

  <section class="benefit-group group-app">
    <svg class="benefit-icon" viewBox="0 0 38 38" aria-hidden="true">
      <circle cx="19" cy="19" r="18" fill="var(--icon)"/>
      <path d="M11 19.5l5.5 5.5L27 13.5" fill="none" stroke="#fff" stroke-width="3.2" stroke-linecap="round" stroke-linejoin="round"/>
    </svg>
    <ul class="benefit-list">
      <li>Tap into the growth market of mobile and online food ordering</li>
      <li>Go mobile with an online food ordering app that is dedicated and designed specifically for your business</li>
      <li>Attractive interactive menus, show-off your business and food to its best</li>
      <li>Easily and quickly update your menu with seasonal changes, menu items, pricing and even delivery options.</li>
    </ul>
  </section>

  <section class="benefit-group group-customer">
    <svg class="benefit-icon" viewBox="0 0 38 38" aria-hidden="true">
      <circle cx="13" cy="12" r="5" fill="var(--icon)"/>
      <circle cx="25" cy="12" r="5" fill="var(--icon)"/>
      <circle cx="19" cy="20" r="5.5" fill="var(--icon)"/>
      <path d="M5 27c0-5 4-8 8-8M33 27c0-5-4-8-8-8" fill="none" stroke="var(--icon)" stroke-width="4"/>
      <path d="M9 35c0-6 4.5-9 10-9s10 3 10 9z" fill="var(--icon)"/>
    </svg>
    <ul class="benefit-list">
      <li>Order history is saved making re-ordering fast and convenient</li>
      <li>Use convenient online payment like KOINRA, traditional credit cards or cash on collection</li>
      <li>Launch an in-app loyalty programme</li>
      <li>We don’t encourage your customer to use a shared app that then promotes your competitors’ businesses to your customers</li>
    </ul>
  </section>

  <section class="benefit-group group-business">
    <svg class="benefit-icon" viewBox="0 0 38 38" aria-hidden="true">
      <path d="M4 6h30v20H16l-7 7v-7H4z" fill="var(--icon)"/>
      <circle cx="12" cy="16" r="2" fill="#fff"/>
      <circle cx="19" cy="16" r="2" fill="#fff"/>
      <circle cx="26" cy="16" r="2" fill="#fff"/>
    </svg>
    <ul class="benefit-list">
      <li>No more holding or busy signal</li>
      <li>Free up your phone line at peak periods, never miss another order</li>
      <li>Save staff time by accepting unlimited mobile and on-line orders simultaneously</li>
      <li>Send promotions to your customers of seasonal opening times or message them each time they are close to your business</li>
      <li>Differentiate your business against other local businesses</li>
      <li>Benefit from better Zintaro search results</li>
    </ul>
  </section>

  <section class="benefit-group group-pricing">
    <svg class="benefit-icon" viewBox="0 0 38 38" aria-hidden="true">
      <circle cx="19" cy="19" r="18" fill="var(--icon)"/>
      <text x="19" y="27" text-anchor="middle" font-family="Open Sans, Arial, sans-serif" font-weight="700" font-size="22" fill="#fff">£</text>
    </svg>
    <ul class="benefit-list">
      <li>We don’t charge order commission. As you grow you keep all the profits!</li>
      <li>We will also provide you an online shop that can be added to your website! (Business or Business Plus package)</li>
      <li>If you’re thinking this isn’t going to be cheap, check our pricing on our web site</li>
    </ul>
  </section>

  <footer class="footer">
    <p class="footer-text">Please call us on 01632 960417 or email us at Info@Tappora-demo.com<br>to discuss your requirements with us.</p>
    <div class="brand">
      <span class="brand-mark"></span>
      <span class="brand-name">Tappora</span>
    </div>
  </footer>
</main>
</body>
</html>
```